Web site for radio show

I've got a radio show starting on OrbitalWave and need a web site for it. I am familiar with WordPress, so I'd like to get a design for a WordPress-based web site for the show.

I'm also posting a logo project to be done at the same time.

The best radio show web site I've seen is the Cosmic Tuesday site (www.cosmictuesday-example.com). That's a good model but I don't want to start with that much complexity and content. The initial site that I'd like you to design would have the following parts:
- Upcoming shows
- Past shows (including links to authors, their web sites, and their books)
- Social feed
- Blog
- About
- ...and anything else you think would be necessary

For colors, I'd like it to be consistent with my personal web site: www.kellaway-ventures-example.com

Target Market(s)

The target market for this show is mid- to upper-level managers

Industry/Entity Type

Radio

Requirements
Must have
• The project has to proceed in (at least) two stages: a first rough layout, and a second finished design. Whether you want a third stage in between with look and feel options is up to you.

```html
<!DOCTYPE html>
<html lang="en">
<head>
<meta charset="utf-8">
<title>Kellaway Show</title>
<link href="https://fonts.googleapis.com/css2?family=Open+Sans:ital,wght@0,400;0,600;1,400;1,600&family=Oswald:wght@400&display=swap" rel="stylesheet">
<style>
:root{
  --red:#b30c0c;
  --grey-logo:#9a9a9a;
  --text:#444;
  --muted:#8a8a8a;
  --panel:#f3f3f3;
  --page-bg:#f4f4f4;
  --line:#dcdcdc;
  --footer:#efefef;
  --icon:#bdbdbd;
}
*{box-sizing:border-box;margin:0;padding:0}
html,body{width:894px;height:1200px;overflow:hidden}
body{background:var(--page-bg);font-family:"Open Sans",sans-serif;color:var(--text);position:relative}
.page{position:absolute;left:90px;top:0;width:715px;height:1093px;background:#fff;box-shadow:0 0 4px rgba(0,0,0,.12)}
.abs{position:absolute}
.logo{left:103px;top:12px;font-family:"Oswald",sans-serif;font-size:31px;line-height:34px;color:var(--red)}
.logo span{display:block;color:var(--grey-logo)}
.search{left:634px;top:18px;width:164px;height:25px;background:#f1f1f1;border:1px solid #ddd;font-size:10px;font-style:italic;color:#aaa;padding:5px 9px}
.search svg{position:absolute;right:5px;top:4px}
.nav{left:320px;top:69px;width:476px;display:flex;justify-content:space-between;font-size:11px;color:#333;letter-spacing:.2px}
.rule{left:97px;top:100px;width:701px;height:4px;background:var(--red)}
.hero{left:97px;top:111px;width:701px;height:288px;background:linear-gradient(90deg,#2a211d 0%,#5a4a40 25%,#3b2c26 40%,#140e0d 60%,#0b0909 100%)}
.hero-copy{position:absolute;right:34px;top:66px;text-align:right;color:#fff}
.hero-copy h1{font-style:italic;font-weight:600;font-size:26px;line-height:31px;color:#c8181c;letter-spacing:.5px;margin-bottom:10px}
.hero-copy p{font-size:10.5px;line-height:14px;font-weight:600}
.btn{display:inline-block;margin-top:28px;background:#555;color:#eee;font-size:10.5px;padding:5px 15px;border-radius:2px}
.dots{display:flex;gap:4px}
.dots i{width:7px;height:7px;border-radius:50%;background:#777}
.dots i.on{background:var(--red)}
.hero .dots{position:absolute;left:324px;top:262px}
.hero .dots i{width:10px;height:10px;background:#bbb}
.hero .dots i.on{background:#fff}
.card{background:#fff;box-shadow:0 0 3px rgba(0,0,0,.2)}
.about{left:97px;top:414px;width:701px;height:140px;text-align:center;padding:16px 26px}
.about h2{font-family:"Oswald",sans-serif;font-weight:400;font-size:20px;color:var(--grey-logo);margin-bottom:12px}
.about h2 b{font-weight:400;color:var(--red)}
.about p{font-size:10px;line-height:17px;color:#555}
.box{background:var(--panel);box-shadow:0 0 3px rgba(0,0,0,.2);width:343px;height:242px}
.box-head{background:var(--red);color:#fff;font-family:"Oswald",sans-serif;font-size:17px;height:28px;line-height:28px;padding-left:11px}
.item{display:flex;gap:14px;margin:0 12px;padding:12px 0 6px}
.item + .item{border-top:1px solid var(--line);padding-top:9px}
.item-text{width:212px}
.thumb{flex:none;width:77px;height:70px;border:2px solid #fff;box-shadow:0 0 2px rgba(0,0,0,.3)}
.date{font-size:10.5px;color:#222;line-height:15px}
.title{font-size:10px;font-weight:600;color:var(--red);line-height:15px}
.desc{font-size:8.8px;color:var(--muted);line-height:15px;margin-top:3px}
.box .dots,.feed .dots{position:absolute;left:50%;transform:translateX(-50%)}
.past-body{padding:11px 12px 0;font-size:8.8px;color:var(--muted);line-height:15px}
.past-body .float{float:left;width:77px;height:70px;margin:2px 14px 2px 0;border:2px solid #fff;box-shadow:0 0 2px rgba(0,0,0,.3)}
.past-body .title{margin-bottom:5px;padding-right:20px}
.meta{clear:both;padding-top:20px;font-size:9px;color:#333;line-height:17px}
.meta div{display:flex;align-items:center;gap:8px}
.meta svg{flex:none}
.feed{width:343px;height:243px;padding:12px 12px 0}
.feed-head{display:flex;align-items:center;gap:10px;font-family:"Oswald",sans-serif;font-size:17px;color:var(--red);padding:0 0 5px 0;border-bottom:1px solid var(--line)}
.feed-head i{width:18px;height:18px;border-radius:50%;background:#999;display:block}
.tweet{display:flex;gap:14px;padding:15px 0 12px;font-size:9px;line-height:15px;color:#333}
.tweet + .tweet{border-top:1px solid var(--line)}
.tweet .thumb{width:60px;height:50px}
.at{color:var(--red)}
.actions{font-style:italic;color:#aaa;font-size:8.5px}
.blog-text{font-size:8.8px;line-height:15px;color:var(--muted);padding-top:14px}
.blog-text .float{float:left;width:98px;height:70px;margin:2px 10px 2px 0;border:2px solid #fff;box-shadow:0 0 2px rgba(0,0,0,.3)}
.blog-text h3{font-size:10px;font-weight:600;color:#222;line-height:15px;margin-bottom:5px}
.blog-text a{color:var(--red);font-style:italic;text-decoration:none;white-space:nowrap}
.footer{left:0;top:1093px;width:894px;height:107px;background:var(--footer)}
.f-logo{left:97px;top:17px;font-family:"Oswald",sans-serif;font-size:19px;line-height:21px;color:var(--red)}
.f-logo span{display:block;color:var(--grey-logo)}
.f-copy{left:97px;top:67px;font-size:9px;color:#555}
.f-head{font-family:"Oswald",sans-serif;font-size:15px;color:var(--red)}
.partner{left:417px;top:14px}
.partner .name{margin-top:6px;display:flex;align-items:center;gap:6px;font-weight:600;font-size:20px;color:#1a4a8a}
.partner .name i{width:14px;height:14px;border-radius:50%;background:#1a4a8a;display:block}
.connect{left:638px;top:14px}
.socials{display:flex;gap:7px;margin-top:8px}
.socials i{width:27px;height:27px;border-radius:50%;background:var(--icon);display:block}
</style>
</head>
<body>
<div class="page"></div>

<div class="abs logo">Kellaway<span>Show</span></div>
<div class="abs search">Search..
  <svg width="18" height="16" viewBox="0 0 18 16"><circle cx="6.5" cy="6.5" r="4.5" fill="none" stroke="#b30c0c" stroke-width="2"/><line x1="10" y1="10" x2="16" y2="14" stroke="#b30c0c" stroke-width="3" stroke-linecap="round"/></svg>
</div>
<nav class="abs nav"><span>HOME</span><span>ABOUT</span><span>LISTEN</span><span>EVENTS</span><span>PAST SHOWS</span><span>BLOG</span><span>DONATE</span></nav>
<div class="abs rule"></div>

<section class="abs hero" role="img" aria-label="Photo of the host speaking on stage with a headset microphone">
  <div class="hero-copy">
    <h1>Helping companies boost<br>innovation..</h1>
    <p>HEAR OWEN SPEAK<br>KEYNOTES, CONFERENCES, SMALL GROUPS</p>
    <span class="btn">Learn more</span>
  </div>
  <div class="dots"><i class="on"></i><i></i><i></i><i></i></div>
</section>

<section class="abs card about">
  <h2>About <b>Kellaway</b> Show</h2>
  <p>Aliquam molestie, mi et imperdiet euismod, dui purus auctor tellus, et interdum lacus lectus et ante. Sed accumsan sollicitudin sapien, sit amet adipiscing turpis gravida ac. In congue, neque ac lobortis volutpat, libero mauris varius mi, vitae suscipit ipsum ligula vitae risus. Duis aliquam nibh a dui iaculis viverra id a velit. Vivamus egestas risus in magna varius commodo. Sed semper viverra egestas. Etiam pretium porttitor lectus, vel ornare neque porta volutpat.</p>
</section>

<section class="abs box" style="left:97px;top:570px">
  <div class="box-head">Upcoming Shows</div>
  <div class="item">
    <div class="thumb" role="img" aria-label="Portrait of the host" style="background:linear-gradient(135deg,#1a1412,#6b5346 60%,#2a201b)"></div>
    <div class="item-text"><div class="date">Feb 10, 2014</div><div class="title">Nam fermentum vestibulum purus id aliquet ultricies et sollicitudin ..</div><div class="desc">Vestibulum vel metus sit amet turpis bibendum tincidunt vel sit amet quam...</div></div>
  </div>
  <div class="item">
    <div class="thumb" role="img" aria-label="Photo of a 3D printer being assembled" style="background:linear-gradient(135deg,#a89a90,#7a2a2a 55%,#c9bdb3)"></div>
    <div class="item-text"><div class="date">Feb 10, 2014</div><div class="title">Nam fermentum vestibulum purus id aliquet ultricies et sollicitudin ..</div><div class="desc">Vestibulum vel metus sit amet turpis bibendum tincidunt vel sit amet quam...</div></div>
  </div>
  <div class="dots" style="top:222px"><i class="on"></i><i></i><i></i><i></i></div>
</section>

<section class="abs box" style="left:455px;top:570px">
  <div class="box-head">Past Shows</div>
  <div class="past-body">
    <div class="float" role="img" aria-label="Photo of the host presenting in front of a projected robot" style="background:linear-gradient(135deg,#5a6e88,#a9c3de 60%,#7c8ea4)"></div>
    <div class="title">Nam fermentum vestibulum purus id aliquet ultricies et sollicitudin ..</div>
    Vestibulum vel metus sit amet turpis bibendum tincidunt vel sit amet quam. Pellentesque habitant morbi tristique senectus... Nunc consequat congue nulla eu imperdiet. Donec in est erat, id male-suada turpis. Nunc a dui id turpis convallis semper.unc dignissim lectus vitae eros placerat euismod. ..
    <div class="meta">
      <div><svg width="9" height="9" viewBox="0 0 9 9"><circle cx="4.5" cy="2.5" r="2.2" fill="#444"/><path d="M0 9c0-3 2-4.5 4.5-4.5S9 6 9 9z" fill="#444"/></svg>By Owen Kellaway <span style="margin:0 2px">|</span><svg width="9" height="9" viewBox="0 0 9 9"><circle cx="4.5" cy="4.5" r="4.5" fill="#444"/><path d="M2 3l2 1 1 2-1 2M6 1.5l-.5 1.5 2 1" stroke="#fff" stroke-width=".9" fill="none"/></svg>www.kellaway-ventures-example.com</div>
      <div><svg width="9" height="9" viewBox="0 0 9 9"><rect x="1" y="0" width="7" height="9" fill="#444"/><rect x="2.5" y="1.5" width="4" height="1" fill="#fff"/></svg>Layer By Layer</div>
    </div>
  </div>
  <div class="dots" style="top:222px"><i class="on"></i><i></i><i></i><i></i></div>
</section>

<section class="abs card feed" style="left:97px;top:827px">
  <div class="feed-head"><i></i>Social Feed</div>
  <div class="tweet">
    <div class="thumb" role="img" aria-label="Photo of the host at a conference" style="background:linear-gradient(135deg,#d8cfc4,#8a7a6c 60%,#c7d0dc)"></div>
    <div>Owen Kellaway@okellaway &nbsp;Feb 5<br><span class="at">@MarenQuill</span> Thanks Maren. &nbsp;Neither a Harborhawks nor Ridgecolts fan.<br><span class="actions">Reply &nbsp;| Retweet &nbsp;| Favorite | More</span></div>
  </div>
  <div class="tweet">
    <div class="thumb" role="img" aria-label="Profile photo" style="background:linear-gradient(135deg,#3a2a22,#9a7560 55%,#e8e4e0)"></div>
    <div>Owen Kellaway@okellaway &nbsp;Feb 5<br><span class="at">@MarenQuill</span> Thanks Maren. &nbsp;Neither a Harborhawks nor Ridgecolts fan.<br><span class="actions">Reply &nbsp;| Retweet &nbsp;| Favorite | More</span></div>
  </div>
  <div class="dots" style="top:226px"><i class="on"></i><i></i><i></i><i></i></div>
</section>

<section class="abs card feed" style="left:455px;top:827px">
  <div class="feed-head"><i></i>Blog Posts</div>
  <div class="blog-text">
    <div class="float" role="img" aria-label="Photo of a man operating a 3D printer" style="background:linear-gradient(135deg,#6e6e72,#a3a6ab 50%,#4a5f80)"></div>
    <h3>Is 3D Printing a Production Technology? Part 1: Making Consumer Products at Home..</h3>
    Some of my colleagues believe that additive manufacturing (of which 3D printing is one type) is only a prototyping technology now. &nbsp;It's an interesting debate that I've been looking into all summer. I believe they're wrong; that there is a significant set of products that are better produced using additive manufacturing techniques right now, both for consumer and industrial applications...<a>Read More</a>
  </div>
  <div class="dots" style="top:226px"><i class="on"></i><i></i><i></i><i></i></div>
</section>

<footer class="abs footer">
  <div class="abs f-logo">Kellaway<span>Show</span></div>
  <div class="abs f-copy">Copyright©. All Right Reserved</div>
  <div class="abs partner"><div class="f-head">Radio Partners</div><div class="name"><i></i>OrbitalWave</div></div>
  <div class="abs connect"><div class="f-head">Connect Us</div><div class="socials"><i></i><i></i><i></i><i></i><i></i></div></div>
</footer>
</body>
</html>
```